TALVORE GROUP OF CLINICS

We need a medical & lab report file. The design should be healthcare related. Our current file design has been used for almost 10 years. We need something more fresh & up-to-date. We have attached the current file design.

Need extra days to review

```html
<!DOCTYPE html>
<html lang="en">
<head>
<meta charset="utf-8">
<title>Talvore Group of Clinics – Medical Report Folder</title>
<link rel="stylesheet" href="https://fonts.googleapis.com/css2?family=Open+Sans:wght@400;600;700;800&family=Italianno&display=swap">
<style>
  :root{
    --bg:#e4e5e7;
    --paper:#f4f5f7;
    --paper-shade:#e6e8ec;
    --blue-deep:#1d4fbf;
    --blue-bright:#2d9fe3;
    --blue-ink:#2e3a9c;
    --sky-band:#aadcf5;
    --navy-img:#0a1a3a;
    --text:#2b2b33;
  }
  *{box-sizing:border-box;margin:0;padding:0}
  html,body{width:1200px;height:847px;overflow:hidden}
  body{background:var(--bg);font-family:"Open Sans",Arial,sans-serif;position:relative}
  .spread{position:absolute;left:20px;top:20px;width:1160px;height:807px;display:flex;box-shadow:0 8px 24px rgba(0,0,0,.18)}
  .page{position:relative;width:580px;height:807px;overflow:hidden;
    background:
      linear-gradient(125deg,transparent 40%,rgba(255,255,255,.7) 41%,transparent 60%),
      linear-gradient(60deg,var(--paper-shade) 0%,var(--paper) 45%,#fff 70%,var(--paper-shade) 100%);}
  .page--back{border-right:1px solid #d2d4d9}
  .edge{position:absolute;left:0;right:0;background:linear-gradient(90deg,var(--blue-deep),var(--blue-bright))}
  .edge--top{top:10px;height:5px}
  .edge--bottom{bottom:12px;height:10px}
  .banner{position:absolute;left:50%;transform:translateX(-50%);
    background:linear-gradient(180deg,var(--blue-bright),var(--blue-deep));
    color:#fff;font-weight:800;text-transform:uppercase;text-align:center;white-space:nowrap;
    box-shadow:0 6px 10px rgba(0,0,0,.25);letter-spacing:.5px}
  .banner--group{top:70px;width:350px;padding:9px 0;font-size:20px}
  .banner--report{top:52px;width:400px;padding:9px 0;font-size:24px}
  .visual{position:absolute;left:0;right:0}
  .visual--brain{top:150px;height:270px;background:radial-gradient(ellipse at 55% 45%,#3f8fe0 0%,#173d86 30%,var(--navy-img) 65%,#050b1c 100%)}
  .visual--heart{top:400px;height:300px;background:radial-gradient(ellipse at 58% 55%,#ff6a3a 0%,#a8241a 22%,#2a0c12 48%,#04060c 75%)}
  .branches{position:absolute;top:440px;left:24px;right:24px;display:grid;grid-template-columns:1fr 1fr;column-gap:20px;row-gap:12px;text-align:center}
  .branch--wide{grid-column:1 / span 2}
  .branch__name{color:var(--blue-ink);font-weight:700;font-size:12px;line-height:17px;text-transform:uppercase;white-space:nowrap}
  .branch__line{color:var(--text);font-size:10px;line-height:13px;white-space:nowrap}
  .tagline-band{position:absolute;top:112px;left:0;right:0;height:50px;background:var(--sky-band);
    display:flex;align-items:center;justify-content:center}
  .tagline{font-family:"Italianno",cursive;color:var(--blue-ink);font-size:40px}
  .brand{position:absolute;top:255px;left:0;right:0;display:flex;align-items:center;justify-content:center;gap:14px}
  .brand__dot{width:44px;height:44px;border-radius:50%;background:var(--blue-deep)}
  .brand__name{color:var(--blue-ink);font-weight:700;font-size:26px;letter-spacing:.5px}
  .confidential{position:absolute;right:34px;top:722px;color:var(--blue-ink);font-weight:600;font-size:22px;letter-spacing:.5px}
</style>
</head>
<body>
<div class="spread">
  <section class="page page--back">
    <div class="edge edge--top"></div>
    <div class="banner banner--group">Talvore Group of Clinics</div>
    <div class="visual visual--brain" role="img" aria-label="Glowing blue illustration of a human head with a brain neural network"></div>
    <div class="branches">
      <div class="branch">
        <div class="branch__name">Pusat Perubatan Talvore</div>
        <div class="branch__line">Level 12, Wisma Seri Tanjung, Jalan Kenari 4,</div>
        <div class="branch__line">50450 Kuala Lumpur</div>
        <div class="branch__line">Tel: +603-5550-0101 Fax: +603-5550-0102</div>
        <div class="branch__line">Email: kl@talvore.example</div>
      </div>
      <div class="branch">
        <div class="branch__name">Klinik Talvore (Bukit Serai)</div>
        <div class="branch__line">No. 8, Jalan Serai Indah 2/4, Bukit Serai,</div>
        <div class="branch__line">40160 Shah Alam, Selangor</div>
        <div class="branch__line">Tel: +603-5550-0211 Fax: +603-5550-0212</div>
        <div class="branch__line">Email: serai@talvore.example</div>
      </div>
      <div class="branch">
        <div class="branch__name">Klinik Talvore (Harbour Point)</div>
        <div class="branch__line">Lot 2-1, Persiaran Harbour Point,</div>
        <div class="branch__line">11960 Penang</div>
        <div class="branch__line">Tel: +604-5550-0321 Fax: +604-5550-0322</div>
        <div class="branch__line">Email: harbour@talvore.example</div>
      </div>
      <div class="branch">
        <div class="branch__name">Klinik Talvore (Seri Damar)</div>
        <div class="branch__line">No. 21, Jalan Pusat Seri Damar 1/2,</div>
        <div class="branch__line">71960 Negeri Sembilan</div>
        <div class="branch__line">Tel: +606-5550-0431 Fax: +606-5550-0432</div>
        <div class="branch__line">Email: damar@talvore.example</div>
      </div>
      <div class="branch">
        <div class="branch__name">Talvore Medical Clinic (Airport T1)</div>
        <div class="branch__line">Unit A4, Arrival Level, Main Terminal,</div>
        <div class="branch__line">64010 Sepang, Selangor</div>
        <div class="branch__line">Tel: +603-5550-0541 Fax: +603-5550-0542</div>
        <div class="branch__line">Email: t1@talvore.example</div>
      </div>
      <div class="branch">
        <div class="branch__name">Talvore Medical Clinic (Airport T2)</div>
        <div class="branch__line">Unit B2, Landside Arrival Level,</div>
        <div class="branch__line">64010 Sepang, Selangor</div>
        <div class="branch__line">Tel: +603-5550-0651 Fax: +603-5550-0652</div>
        <div class="branch__line">Email: t2@talvore.example</div>
      </div>
      <div class="branch branch--wide">
        <div class="branch__name">Talvore Medical Clinic (North Airport)</div>
        <div class="branch__line">Level 1, Passenger Terminal Building,</div>
        <div class="branch__line">11960 Penang</div>
        <div class="branch__line">Tel: +604-5550-0761 Fax: +604-5550-0762</div>
        <div class="branch__line">Email: north@talvore.example</div>
      </div>
    </div>
    <div class="edge edge--bottom"></div>
  </section>

  <section class="page page--front">
    <div class="edge edge--top"></div>
    <div class="banner banner--report">Medical Report</div>
    <div class="tagline-band"><span class="tagline">“Your Healthcare Partner”</span></div>
    <div class="brand">
      <span class="brand__dot"></span>
      <span class="brand__name">TALVORE GROUP</span>
    </div>
    <div class="visual visual--heart" role="img" aria-label="Glowing red illustration of the human heart and blood vessels in a torso"></div>
    <div class="confidential">PRIVATE &amp; CONFIDENTIAL</div>
    <div class="edge edge--bottom"></div>
  </section>
</div>
</body>
</html>
```